KLORA product web page

We need a new web design for our KLORA product page. You can find more information about the project on the current web site - www.klora.example

What we need from a new design (uncoded):
- landing pages + template
- all information on one page
- the design should be focused on the product - light bulb + app
- web site should be with some dynamics like a background with parallax effect in the current version
- fonts should be chosen
- a number of illustrations should be designed

Here is schema for a new design: https://files.examplehost.net/d/draw-7QpX2mLk9RtYv4Hs/edit

Here is a document with all texts for a new design: https://files.examplehost.net/d/doc-3WnZ8bJf5KcUe1Ga/edit

Illustrations to use:
v1 - https://files.examplehost.net/f/fold-A1kT9pQw2ZxR
v2 - https://files.examplehost.net/f/fold-B7mH4sLv6YcN

iOS screens: https://files.examplehost.net/f/fold-C3rJ8dKe1WuP

KLORA logo: https://files.examplehost.net/f/fold-D5nF2gTb9XoM
Updates

I forgot to add the definition text "KLORA - is.." to the document with texts. Sorry, my mistake.

Target Market(s)

25-45 year old adults who are interested in "smart" devices for their health.

Industry/Entity Type

Brintel

Colors

Designer to choose colors to be used in the design.

Requirements
Must have
• - landing pages + template
- fonts should be chosen

```html
<!DOCTYPE html>
<html lang="en">
<head>
<meta charset="utf-8">
<title>KLORA — Technical Specifications</title>
<link href="https://fonts.googleapis.com/css2?family=Lato:wght@400;700&display=swap" rel="stylesheet">
<style>
  :root {
    --band-light: #c5e5b8;
    --white: #ffffff;
    --brand: #6cbf4a;
    --page: #8bcb6e;
    --footer: #78b461;
    --ink-dark: #3f6e2a;
    --ink-body: #3b6628;
    --icon: #4f9f2f;
    --nav-ink: #1a1a1a;
    --panel: #aedb96;
    --panel-ink: #5b9743;
    --footer-ink: #cfe9c2;
    --dot: #c5e5b8;
  }
  * { box-sizing: border-box; margin: 0; padding: 0; }
  html, body { width: 1200px; height: 1000px; overflow: hidden; }
  body { font-family: "Lato", Arial, sans-serif; background: var(--page); position: relative; }

  .site-header { position: absolute; top: 0; left: 0; width: 1200px; height: 120px; background: var(--band-light); }
  .site-header__bar { position: absolute; top: 30px; left: 0; width: 100%; height: 60px; background: var(--white); }
  .brand-mark {
    position: absolute; left: 141px; top: 20px; width: 80px; height: 80px; border-radius: 50%;
    background: var(--brand); color: var(--white); font-weight: 700; font-size: 15px;
    letter-spacing: 1px; display: flex; align-items: center; justify-content: center;
  }
  .main-nav { position: absolute; right: 140px; top: 30px; height: 60px; display: flex; align-items: center; gap: 52px; }
  .main-nav a { color: var(--nav-ink); text-decoration: none; font-size: 22px; letter-spacing: 4px; }
  .main-nav a.is-accent { color: var(--brand); font-weight: 700; }

  .section-dots { position: absolute; left: 20px; top: 459px; list-style: none; }
  .section-dots li { width: 15px; height: 15px; border-radius: 50%; background: var(--dot); margin-bottom: 15px; }
  .section-dots li.is-active { background: var(--white); }

  .specs__title {
    position: absolute; top: 232px; left: 0; width: 1200px; text-align: center;
    color: var(--ink-dark); font-size: 25px; font-weight: 700; letter-spacing: 9px;
  }
  .spec { position: absolute; top: 361px; width: 300px; }
  .spec--socket { left: 131px; }
  .spec--temperature { left: 450px; }
  .spec--led { left: 770px; }
  .spec__icon {
    width: 140px; height: 140px; border-radius: 50%; background: var(--white);
    margin: 0 auto; display: flex; align-items: center; justify-content: center;
  }
  .spec__name { margin-top: 44px; text-align: center; color: var(--ink-dark); font-size: 22px; font-weight: 700; }
  .spec__text { margin-top: 14px; color: var(--ink-body); font-size: 16px; line-height: 25px; letter-spacing: 0.3px; }
  .spec__text small { font-size: 12px; }

  .compat {
    position: absolute; left: 327px; top: 750px; width: 547px; height: 90px; background: var(--panel);
    color: var(--panel-ink); text-align: center; font-size: 14px; line-height: 21px; padding-top: 14px;
  }
  .compat strong { display: block; font-weight: 700; }

  .site-footer { position: absolute; left: 0; top: 961px; width: 1200px; height: 39px; background: var(--footer); }
  .site-footer__link { position: absolute; left: 141px; top: 11px; color: var(--footer-ink); font-size: 14px; font-weight: 700; text-decoration: none; }
  .site-footer__copy { position: absolute; right: 148px; top: 10px; color: var(--footer-ink); font-size: 11px; display: flex; align-items: center; gap: 10px; }
  .site-footer__copy b { font-size: 17px; font-weight: 700; letter-spacing: 1px; }
</style>
</head>
<body>
  <header class="site-header">
    <div class="site-header__bar"></div>
    <div class="brand-mark">KLORA</div>
    <nav class="main-nav">
      <a href="#" class="is-accent">PRE-ORDER</a>
      <a href="#">BLOG</a>
      <a href="#">CONTACTS</a>
      <a href="#">RU</a>
    </nav>
  </header>

  <ul class="section-dots">
    <li></li><li></li><li></li><li></li><li></li><li class="is-active"></li>
  </ul>

  <main class="specs">
    <h1 class="specs__title">TECHNICAL SPECIFICATIONS</h1>

    <article class="spec spec--socket">
      <div class="spec__icon">
        <svg width="50" height="72" viewBox="0 0 50 72" fill="var(--icon)">
          <path d="M25 1C12 1 2 10 2 23c0 9 5 14 9 19v6h28v-6c4-5 9-10 9-19C48 10 38 1 25 1z"/>
          <rect x="14" y="52" width="22" height="4" rx="1"/>
          <rect x="14" y="59" width="22" height="4" rx="1"/>
          <rect x="21" y="66" width="8" height="4" rx="1"/>
        </svg>
      </div>
      <h2 class="spec__name">E27 socket</h2>
      <p class="spec__text">No need to change anything. Easy way to home automation at hand. And yes, you can still use those switches.</p>
    </article>

    <article class="spec spec--temperature">
      <div class="spec__icon">
        <svg width="34" height="76" viewBox="0 0 34 76">
          <path d="M11 6a6 6 0 0 1 12 0v44a14 14 0 1 1-12 0z" fill="none" stroke="var(--icon)" stroke-width="4"/>
          <circle cx="17" cy="61" r="10" fill="var(--band-light)"/>
          <rect x="15" y="28" width="4" height="28" fill="var(--band-light)"/>
          <g stroke="var(--icon)" stroke-width="3">
            <line x1="13" y1="16" x2="18" y2="16"/><line x1="13" y1="23" x2="18" y2="23"/>
            <line x1="13" y1="30" x2="18" y2="30"/><line x1="13" y1="37" x2="18" y2="37"/>
          </g>
        </svg>
      </div>
      <h2 class="spec__name">2700-5500K</h2>
      <p class="spec__text">You are not limited in your choice of color temperature. Turn on warm or cold light depending on your activities.</p>
    </article>

    <article class="spec spec--led">
      <div class="spec__icon">
        <svg width="70" height="70" viewBox="0 0 70 70" stroke="var(--icon)" stroke-linecap="round" fill="none">
          <circle cx="35" cy="35" r="10" stroke-width="6"/>
          <g stroke-width="6">
            <line x1="35" y1="4" x2="35" y2="10"/><line x1="35" y1="60" x2="35" y2="66"/>
            <line x1="4" y1="35" x2="10" y2="35"/><line x1="60" y1="35" x2="66" y2="35"/>
            <line x1="14" y1="14" x2="18" y2="18"/><line x1="52" y1="52" x2="56" y2="56"/>
            <line x1="56" y1="14" x2="52" y2="18"/><line x1="14" y1="56" x2="18" y2="52"/>
          </g>
        </svg>
      </div>
      <h2 class="spec__name">LED lighbulb</h2>
      <p class="spec__text">12.5W <small>(110-230V, 50Hz)</small>, 1000lm+: energy efficient LED lightbulb KLORA shines brighter than others and saves energy.</p>
    </article>

    <aside class="compat">
      <strong>Compatibility:</strong>
      Fonix 4S/5/5C/5S - Tablo 3/4/Air/mini/mini Air - Pocketa 5th generation or newer<br>
      All Droidra devices with ShortLink 2.1 or 4
    </aside>
  </main>

  <footer class="site-footer">
    <a href="#" class="site-footer__link">CONTACTS</a>
    <div class="site-footer__copy">COPYRIGHT © <b>KLORA</b></div>
  </footer>
</body>
</html>
```